Logo, Web and Mobile Designs for enterprise social media platform

All the details are in the attached document, please start reading the scope document first which explains what is this project about and the details about the needed deliverables, after that please read the UI_Requirements document which will detail what is expected regarding the coded web version since this is a coded contest, it is very important that you meet the UI requirements or suggest something else but we will need to agree first before working on the coded version

Good Luck

Target Market(s)

Enterprise Social Media

Industry/Entity Type

Media

Coding

Coded - Design and coding required

Number of Pages Required

5+ page

Font styles to use
Sans Serif

Requirements
Must have
• All the must haves are listed in the scope document so please check before you start

```html
<!DOCTYPE html>
<html lang="en">
<head>
<meta charset="utf-8">
<title>Teamora – Event Members</title>
<link href="https://fonts.googleapis.com/css2?family=Roboto:wght@300;400;500&family=Roboto+Condensed:wght@400&display=swap" rel="stylesheet">
<style>
:root{
  --page-bg:#f6f6f6;
  --white:#ffffff;
  --row-bg:#f4f5f7;
  --line:#e1e3e6;
  --text:#555a60;
  --text-dark:#4a4f55;
  --muted:#7a7e83;
  --brand:#1b8ac2;
  --brand-soft:#2aa3d4;
  --footer:#1d8ab5;
  --avatar:#c9a58a;
}
*{box-sizing:border-box;margin:0;padding:0}
html,body{width:1200px;height:3470px;overflow:hidden}
body{background:var(--page-bg);font-family:'Roboto',Arial,sans-serif;color:var(--text);position:relative}

.site-header{position:absolute;left:0;top:0;width:1200px;height:232px;background:var(--white);border-bottom:3px solid var(--line);display:flex}
.header-cell{width:217px;height:100%;display:flex;align-items:center;justify-content:center}
.header-cell.home{border-right:2px solid var(--line)}
.header-cell.menu{margin-left:auto;width:208px;border-left:2px solid var(--line)}
.brand{position:absolute;left:350px;top:0;height:229px;display:flex;align-items:center;gap:22px}
.brand-mark{width:80px;height:80px;border-radius:50%;background:var(--brand-soft)}
.brand-name{font-size:72px;font-weight:500;color:var(--brand);letter-spacing:1px}

.panel{position:absolute;left:45px;top:310px;width:1112px;height:2715px;background:var(--white);border:2px solid var(--line)}
.nav-list{list-style:none;display:flex;flex-direction:column;gap:7px}
.nav-item{height:143px;background:var(--row-bg);border:2px solid var(--line);display:flex;align-items:center;position:relative;font-size:40px;font-weight:300;color:var(--text-dark);text-transform:uppercase}
.nav-item .lead{position:absolute;left:72px;top:50%;transform:translateY(-50%)}
.nav-item .label{margin-left:160px}
.nav-item .toggle{position:absolute;right:40px;top:50%;transform:translateY(-50%)}

.members-card{position:absolute;left:43px;top:2208px;width:1022px;height:730px;border:2px solid var(--line);background:var(--white)}
.card-head{height:145px;background:var(--row-bg);border-bottom:2px solid #d4d7db;display:flex;align-items:center;padding-left:58px;gap:28px;font-size:44px;font-weight:300;color:var(--text-dark);text-transform:uppercase}
.field-label{position:absolute;left:65px;font-size:40px;font-weight:400;color:var(--text)}
.member-box{position:absolute;left:65px;width:875px;height:110px;border:2px solid var(--line);border-radius:5px;box-shadow:0 2px 3px rgba(0,0,0,.06);display:flex;align-items:center;padding-left:30px;gap:20px;font-size:33px;color:#333}
.avatar{width:60px;height:60px;background:linear-gradient(135deg,#b8906f,var(--avatar));border-radius:3px}
.remove-btn{position:absolute;right:20px;top:19px;width:68px;height:68px;background:var(--brand);display:flex;align-items:center;justify-content:center}
.remove-btn span{width:20px;height:4px;background:var(--white)}

.site-footer{position:absolute;left:0;top:3105px;width:1200px;height:365px;background:var(--footer);color:var(--white);text-align:center}
.social{display:flex;justify-content:center;gap:27px;margin-top:75px}
.social span{width:58px;height:58px;border-radius:8px;background:var(--white)}
.footer-links{font-family:'Roboto Condensed',Arial,sans-serif;font-size:36px;margin-top:32px;word-spacing:4px}
.footer-links a{color:var(--white);text-decoration:none}
.footer-links .sep{margin:0 18px}
.copyright{font-size:33px;margin-top:32px}
</style>
</head>
<body>

<header class="site-header">
  <div class="header-cell home">
    <svg width="52" height="44" viewBox="0 0 26 22" aria-label="Home"><path d="M13 1 L1 11 h3 v10 h7 v-6 h4 v6 h7 V11 h3z" fill="#6d7176"/></svg>
  </div>
  <div class="brand"><span class="brand-mark"></span><span class="brand-name">Teamora</span></div>
  <div class="header-cell menu">
    <svg width="52" height="44" viewBox="0 0 26 22" aria-label="Menu"><rect y="2" width="26" height="4" fill="#6d7176"/><rect y="9" width="26" height="4" fill="#6d7176"/><rect y="16" width="26" height="4" fill="#6d7176"/></svg>
  </div>
</header>

<main class="panel">
  <ul class="nav-list">
    <li class="nav-item"><svg class="lead" width="46" height="40" viewBox="0 0 23 20"><rect width="10" height="9" rx="1" fill="var(--brand)"/><rect x="12" width="11" height="9" rx="1" fill="var(--brand)"/><rect y="11" width="10" height="9" rx="1" fill="var(--brand)"/><rect x="12" y="11" width="11" height="9" rx="1" fill="var(--brand)"/></svg><span class="label">View Dashboard</span></li>
    <li class="nav-item"><svg class="lead" width="42" height="44" viewBox="0 0 21 22"><rect x="1" y="3" width="19" height="18" fill="none" stroke="var(--brand)" stroke-width="2"/><rect x="1" y="3" width="19" height="5" fill="var(--brand)"/><path d="M5 11h3v3H5zM9 11h3v3H9zM13 11h3v3h-3zM5 15h3v3H5zM9 15h3v3H9zM13 15h3v3h-3z" fill="var(--brand)"/><rect x="5" y="0" width="2" height="5" fill="var(--brand)"/><rect x="14" y="0" width="2" height="5" fill="var(--brand)"/></svg><span class="label">View Event</span><svg class="toggle" width="24" height="24" viewBox="0 0 12 12"><path d="M2 6 L6 2 L10 6 M2 10 L6 6 L10 10" fill="none" stroke="#555" stroke-width="1.6"/></svg></li>
    <li class="nav-item"><svg class="lead" width="18" height="28" viewBox="0 0 9 14"><path d="M1 1 L7 7 L1 13" fill="none" stroke="var(--brand)" stroke-width="2"/></svg><span class="label">About Us</span><svg class="toggle" width="24" height="24" viewBox="0 0 12 12"><path d="M2 6 L6 2 L10 6 M2 10 L6 6 L10 10" fill="none" stroke="#555" stroke-width="1.6"/></svg></li>
    <li class="nav-item"><svg class="lead" width="18" height="28" viewBox="0 0 9 14"><path d="M1 1 L7 7 L1 13" fill="none" stroke="var(--brand)" stroke-width="2"/></svg><span class="label">Speakers</span><svg class="toggle" width="24" height="24" viewBox="0 0 12 12"><path d="M2 6 L6 2 L10 6 M2 10 L6 6 L10 10" fill="none" stroke="#555" stroke-width="1.6"/></svg></li>
    <li class="nav-item"><svg class="lead" width="18" height="28" viewBox="0 0 9 14"><path d="M1 1 L7 7 L1 13" fill="none" stroke="var(--brand)" stroke-width="2"/></svg><span class="label">Track</span><svg class="toggle" width="24" height="24" viewBox="0 0 12 12"><path d="M2 6 L6 2 L10 6 M2 10 L6 6 L10 10" fill="none" stroke="#555" stroke-width="1.6"/></svg></li>
    <li class="nav-item"><svg class="lead" width="18" height="28" viewBox="0 0 9 14"><path d="M1 1 L7 7 L1 13" fill="none" stroke="var(--brand)" stroke-width="2"/></svg><span class="label">Sessions</span><svg class="toggle" width="24" height="24" viewBox="0 0 12 12"><path d="M2 6 L6 2 L10 6 M2 10 L6 6 L10 10" fill="none" stroke="#555" stroke-width="1.6"/></svg></li>
    <li class="nav-item"><svg class="lead" width="18" height="28" viewBox="0 0 9 14"><path d="M1 1 L7 7 L1 13" fill="none" stroke="var(--brand)" stroke-width="2"/></svg><span class="label">Tickets</span><svg class="toggle" width="24" height="24" viewBox="0 0 12 12"><path d="M2 6 L6 2 L10 6 M2 10 L6 6 L10 10" fill="none" stroke="#555" stroke-width="1.6"/></svg></li>
    <li class="nav-item"><svg class="lead" width="18" height="28" viewBox="0 0 9 14"><path d="M1 1 L7 7 L1 13" fill="none" stroke="var(--brand)" stroke-width="2"/></svg><span class="label">Organizers</span><svg class="toggle" width="24" height="24" viewBox="0 0 12 12"><path d="M2 6 L6 2 L10 6 M2 10 L6 6 L10 10" fill="none" stroke="#555" stroke-width="1.6"/></svg></li>
    <li class="nav-item"><svg class="lead" width="18" height="28" viewBox="0 0 9 14"><path d="M1 1 L7 7 L1 13" fill="none" stroke="var(--brand)" stroke-width="2"/></svg><span class="label">Sponsors</span><svg class="toggle" width="24" height="24" viewBox="0 0 12 12"><path d="M2 6 L6 2 L10 6 M2 10 L6 6 L10 10" fill="none" stroke="#555" stroke-width="1.6"/></svg></li>
    <li class="nav-item"><svg class="lead" width="18" height="28" viewBox="0 0 9 14"><path d="M1 1 L7 7 L1 13" fill="none" stroke="var(--brand)" stroke-width="2"/></svg><span class="label">Exhibitor</span><svg class="toggle" width="24" height="24" viewBox="0 0 12 12"><path d="M2 6 L6 2 L10 6 M2 10 L6 6 L10 10" fill="none" stroke="#555" stroke-width="1.6"/></svg></li>
    <li class="nav-item"><svg class="lead" width="18" height="28" viewBox="0 0 9 14"><path d="M1 1 L7 7 L1 13" fill="none" stroke="var(--brand)" stroke-width="2"/></svg><span class="label">Security</span><svg class="toggle" width="24" height="24" viewBox="0 0 12 12"><path d="M2 6 L6 2 L10 6 M2 10 L6 6 L10 10" fill="none" stroke="#555" stroke-width="1.6"/></svg></li>
    <li class="nav-item"><svg class="lead" width="18" height="28" viewBox="0 0 9 14"><path d="M1 1 L7 7 L1 13" fill="none" stroke="var(--brand)" stroke-width="2"/></svg><span class="label">Members</span><svg class="toggle" width="24" height="24" viewBox="0 0 12 12"><path d="M2 2 L6 6 L10 2 M2 6 L6 10 L10 6" fill="none" stroke="#555" stroke-width="1.6"/></svg></li>
  </ul>

  <section class="members-card" style="top:1866px">
    <div class="card-head">
      <svg width="34" height="36" viewBox="0 0 21 22"><rect x="1" y="3" width="19" height="18" fill="none" stroke="#5b6067" stroke-width="2"/><rect x="1" y="3" width="19" height="5" fill="#5b6067"/><path d="M5 11h3v3H5zM9 11h3v3H9zM13 11h3v3h-3zM5 15h3v3H5zM9 15h3v3H9zM13 15h3v3h-3z" fill="#5b6067"/></svg>
      <span>Event Members</span>
    </div>
    <p class="field-label" style="top:198px">Members :</p>
    <div class="member-box" style="top:272px">
      <span class="avatar" role="img" aria-label="Member profile photo"></span>
      <span class="member-name">m.karimi</span>
      <span class="remove-btn"><span></span></span>
    </div>
    <p class="field-label" style="top:440px">Administrators :</p>
    <div class="member-box" style="top:515px">
      <span class="avatar" role="img" aria-label="Administrator profile photo"></span>
      <span class="member-name">m.karimi</span>
      <span class="remove-btn"><span></span></span>
    </div>
  </section>
</main>

<footer class="site-footer">
  <div class="social"><span></span><span></span><span></span><span></span><span></span></div>
  <nav class="footer-links">
    <a href="#">Home</a><span class="sep">/</span><a href="#">Contact</a><span class="sep">/</span><a href="#">Topics</a><span class="sep">/</span><a href="#">Posts &amp; Comments</a><span class="sep">/</span><a href="#">Videos Links</a>
  </nav>
  <p class="copyright">Copyright @ 2015 - 2015.Teamora. All Rights Reserved.</p>
</footer>

</body>
</html>
```